Flyer for the Radiant Harvest Worship Day

I am looking to create a flyer for a one day prayer retreat our church is organizing.
This flyer will be posted on social media, websites and will also be printed so it can be mailed to people.
I am looking for something professional, with good use of our logo and band colors (logo colors).
I am counting on the designer's skill, creativity, art and knowledge of media communication to produce a flyer that will effectively and quickly convey the message we are trying to spread.
CONTENT OF THE FLYER:
Event title: Radiant Harvest Worship Day
Date: Tuesday July 2nd, 2019
Time: 11:00AM - 7:00PM
Belmora Hotel, 4875 Wexley Avenue, Portland, Maine 04102 (Room: Juniper)
Event Key words to highlight what the event is about: Prayer, Sharing the Word, Panel discussion, prophecy, Impartation.
Key phrases:
A one day prayer retreat.
Jesus Chris is Lord
Contact info:
www.tolvex.org
Phone: 207 555 3184
Email: contact@brookhavenfold.org

```html
<!DOCTYPE html>
<html lang="en">
<head>
<meta charset="utf-8">
<title>Radiant Harvest Worship Day</title>
<link rel="stylesheet" href="https://fonts.googleapis.com/css2?family=Arimo:wght@400;700&family=Roboto:wght@300;400&display=swap">
<style>
  :root {
    --navy: #0b3358;
    --navy-deep: #0a2c4d;
    --orange: #f39321;
    --cream: #fbf4c4;
    --white: #ffffff;
    --gold: #c9973a;
    --page: #ffffff;
    --edge: #6b6b6b;
  }
  * { margin: 0; padding: 0; box-sizing: border-box; }
  html, body { width: 882px; height: 1200px; overflow: hidden; background: var(--page); }
  .canvas { position: relative; width: 882px; height: 1200px; }
  .flyer {
    position: absolute; left: 51px; top: 48px; width: 748px; height: 1059px;
    background: var(--navy); border: 1px solid var(--edge); overflow: hidden;
  }
  .top-band { position: absolute; left: 0; top: 0; width: 100%; height: 27px; background: var(--navy-deep); }
  .hero-photo {
    position: absolute; left: 0; top: 27px; width: 100%; height: 478px;
    background:
      radial-gradient(ellipse at 40% 55%, #caa06f 0%, rgba(202,160,111,0) 45%),
      radial-gradient(ellipse at 70% 45%, #d8b496 0%, rgba(216,180,150,0) 50%),
      linear-gradient(135deg, #5a4030 0%, #8a6a50 45%, #6b5446 70%, #3e3a4e 100%);
  }
  .title-band { position: absolute; left: 0; top: 509px; width: 100%; height: 140px; background: var(--orange); }
  .brand-block {
    position: absolute; left: 59px; top: 0; width: 183px; height: 140px; background: var(--navy);
    display: flex; align-items: center; justify-content: center; gap: 8px;
  }
  .brand-dot { width: 14px; height: 14px; border-radius: 50%; background: var(--orange); }
  .brand-name { font-family: "Arimo", sans-serif; font-weight: 700; font-size: 30px; color: var(--white); letter-spacing: 1px; }
  .event-title {
    position: absolute; left: 253px; top: 18px; width: 490px;
    font-family: "Arimo", sans-serif; font-weight: 700; color: var(--white); line-height: 1;
  }
  .event-title .line-one { display: block; font-size: 40px; letter-spacing: 0.5px; }
  .event-title .line-two { display: block; font-size: 57px; margin-top: 6px; }
  .details { position: absolute; left: 0; top: 649px; width: 100%; height: 410px; }
  .tagline {
    position: absolute; top: 16px; width: 100%; text-align: center;
    font-family: "Roboto", sans-serif; font-weight: 300; font-size: 30px; color: var(--white);
  }
  .confession {
    position: absolute; top: 54px; left: 78px; width: 592px;
    display: flex; align-items: center; gap: 10px;
    font-family: "Roboto", sans-serif; font-weight: 300; font-size: 45px; color: var(--cream); white-space: nowrap;
  }
  .confession .rule { flex: 1; height: 1px; background: var(--white); }
  .event-info {
    position: absolute; top: 124px; width: 100%; text-align: center;
    font-family: "Roboto", sans-serif; font-weight: 300; font-size: 21px; line-height: 33px; color: var(--white);
  }
  .icon { position: absolute; }
  .contact-icons { position: absolute; top: 310px; left: 0; width: 100%; height: 24px; }
  .contact-line {
    position: absolute; top: 336px; width: 100%; text-align: center;
    font-family: "Roboto", sans-serif; font-weight: 400; font-size: 23px; line-height: 30px; color: var(--white); word-spacing: 2px;
  }
</style>
</head>
<body>
<div class="canvas">
  <div class="flyer">
    <div class="top-band"></div>
    <div class="hero-photo" role="img" aria-label="Photo of many open hands reaching together around a wooden cross on a table"></div>

    <div class="title-band">
      <div class="brand-block">
        <span class="brand-dot"></span>
        <span class="brand-name">TOLVEX</span>
      </div>
      <h1 class="event-title">
        <span class="line-one">RADIANT HARVEST</span>
        <span class="line-two">WORSHIP DAY</span>
      </h1>
    </div>

    <div class="details">
      <p class="tagline">A one day prayer retreat.</p>
      <p class="confession"><span class="rule"></span>Jesus Chris is Lord<span class="rule"></span></p>

      <svg class="icon" style="left:170px;top:149px" width="24" height="24" viewBox="0 0 24 24" fill="none" stroke="var(--gold)" stroke-width="1.3">
        <rect x="2" y="4" width="20" height="18"/><line x1="2" y1="9" x2="22" y2="9"/>
        <line x1="7" y1="2" x2="7" y2="6"/><line x1="17" y1="2" x2="17" y2="6"/>
        <line x1="2" y1="14" x2="22" y2="14"/><line x1="2" y1="18" x2="22" y2="18"/>
        <line x1="8" y1="9" x2="8" y2="22"/><line x1="14" y1="9" x2="14" y2="22"/>
      </svg>
      <svg class="icon" style="left:203px;top:180px" width="24" height="24" viewBox="0 0 24 24" fill="none" stroke="var(--gold)" stroke-width="1.3">
        <circle cx="12" cy="13" r="8"/><polyline points="12,8 12,13 15,15"/>
        <line x1="5" y1="4" x2="8" y2="2"/><line x1="19" y1="4" x2="16" y2="2"/>
      </svg>
      <svg class="icon" style="left:136px;top:218px" width="22" height="28" viewBox="0 0 22 28" fill="none" stroke="var(--gold)" stroke-width="1.3">
        <path d="M11 26 C5 18 3 14 3 10 a8 8 0 0 1 16 0 c0 4 -2 8 -8 16z"/><circle cx="11" cy="10" r="3"/>
      </svg>

      <p class="event-info">
        Date: Tuesday July 2nd, 2019<br>
        Time: 11:00AM - 7:00PM<br>
        Belmora Hotel, 4875 Wexley Avenue,<br>
        Portland, Maine 04102 (Room: Juniper)
      </p>

      <div class="contact-icons">
        <svg class="icon" style="left:106px;top:0" width="24" height="24" viewBox="0 0 24 24" fill="none" stroke="var(--white)" stroke-width="1.3">
          <circle cx="12" cy="12" r="10"/><ellipse cx="12" cy="12" rx="4.5" ry="10"/>
          <line x1="2" y1="12" x2="22" y2="12"/><line x1="4" y1="6.5" x2="20" y2="6.5"/><line x1="4" y1="17.5" x2="20" y2="17.5"/>
        </svg>
        <svg class="icon" style="left:272px;top:0" width="26" height="22" viewBox="0 0 26 22" fill="none" stroke="var(--white)" stroke-width="1.3">
          <path d="M2 8 C2 3 24 3 24 8 l-4 2 -3 -3 H9 l-3 3z"/>
          <path d="M6 10 L4 20 H22 L20 10"/><circle cx="13" cy="15" r="3"/>
        </svg>
        <svg class="icon" style="left:518px;top:0" width="28" height="22" viewBox="0 0 28 22" fill="none" stroke="var(--white)" stroke-width="1.3">
          <rect x="2" y="3" width="20" height="14"/><polyline points="2,3 12,11 22,3"/>
          <circle cx="22" cy="16" r="4.5"/><polyline points="20,16 21.5,17.5 24,14.5"/>
        </svg>
      </div>

      <p class="contact-line">tolvex.org &nbsp;|&nbsp; 207 555 3184 &nbsp;|&nbsp; contact@brookhavenfold.org</p>
    </div>
  </div>
</div>
</body>
</html>
```